Corporate Business Card

Very professional, Modern, Not to busy, include phone address email, website
(253) 617-4930, 18761 52nd Avenue S, Kent, WA 98047, martin@plumlinegroup.com, varkoworks.com

Target Market(s)

Manufacturing

Industry/Entity Type

Aero, machining, manufacturing, Off road racing

Contact Information for Business Card

Phone, address email, website

```html
<!DOCTYPE html>
<html lang="en">
<head>
<meta charset="utf-8">
<title>Varko Works – Business Card</title>
<link rel="stylesheet" href="https://fonts.googleapis.com/css2?family=Montserrat:ital,wght@0,500;0,700;1,800&display=swap">
<style>
  :root {
    --page-bg: #f5f5f5;
    --navy: #273d74;
    --red: #d0262b;
    --white: #ffffff;
    --ink: #1b1b1b;
    --rule: #4a4a4a;
  }
  * { margin: 0; padding: 0; box-sizing: border-box; }
  html, body {
    width: 1200px; height: 1057px; overflow: hidden;
    background: var(--page-bg);
    font-family: "Montserrat", Arial, sans-serif;
  }
  .card {
    position: absolute;
    left: 323px;
    width: 533px;
    height: 305px;
    overflow: hidden;
  }
  .card--front { top: 182px; background: var(--navy); }
  .card--back  { top: 548px; background: var(--white); }

  .brand-name {
    position: absolute;
    font-weight: 700;
    white-space: nowrap;
    letter-spacing: 0.02em;
  }
  .card--front .brand-name {
    left: 0; right: 0; top: 128px;
    text-align: center;
    font-size: 40px;
    color: var(--white);
  }
  .card--back .brand-name {
    left: 40px; width: 180px; top: 138px;
    text-align: center;
    font-size: 22px;
    color: var(--navy);
  }

  .corner { position: absolute; left: 0; top: 0; }

  .divider {
    position: absolute;
    left: 251px; top: 72px;
    width: 1px; height: 160px;
    background: var(--rule);
  }

  .person { position: absolute; left: 290px; top: 83px; }
  .person__name {
    font-size: 27px; font-weight: 700; color: var(--navy);
    line-height: 1; letter-spacing: -0.01em;
  }
  .person__role {
    margin-top: 4px;
    font-size: 10.5px; font-weight: 800; font-style: italic;
    color: var(--red); letter-spacing: 0.18em;
  }

  .contact-list {
    position: absolute; left: 290px; top: 143px;
    list-style: none;
  }
  .contact-list li {
    display: flex; align-items: center;
    height: 20.5px;
    font-size: 10px; font-weight: 500; color: var(--ink);
  }
  .contact-list svg { width: 10px; height: 10px; margin-right: 7px; flex: none; }
</style>
</head>
<body>

  <section class="card card--front">
    <div class="brand-name">VARKO WORKS</div>
  </section>

  <section class="card card--back">
    <svg class="corner" width="533" height="305" viewBox="0 0 533 305">
      <polygon points="0,0 67,0 0,51" fill="var(--red)"/>
      <polygon points="533,253 533,305 465,305" fill="var(--navy)"/>
    </svg>

    <div class="brand-name">VARKO WORKS</div>
    <div class="divider"></div>

    <div class="person">
      <div class="person__name">Your Name</div>
      <div class="person__role">POSITION</div>
    </div>

    <ul class="contact-list">
      <li>
        <svg viewBox="0 0 10 10"><path d="M2.2 0.6 L3.6 2.4 L2.8 3.4 Q3.8 5.6 6 6.8 L7 6 L9 7.4 L8.2 9.2 Q4.5 9.2 1.6 5.8 Q0.4 3.4 0.8 1.4 Z" fill="var(--ink)"/></svg>
        (253) 617-4930, 18761
      </li>
      <li>
        <svg viewBox="0 0 10 10"><path d="M5 0.3 A3.6 3.6 0 0 1 8.6 3.9 C8.6 6.3 5 9.7 5 9.7 C5 9.7 1.4 6.3 1.4 3.9 A3.6 3.6 0 0 1 5 0.3 Z M5 2.4 A1.5 1.5 0 1 0 5 5.4 A1.5 1.5 0 1 0 5 2.4 Z" fill="var(--ink)" fill-rule="evenodd"/></svg>
        18761 52nd Avenue S, Kent, WA 98047
      </li>
      <li>
        <svg viewBox="0 0 10 10" fill="none" stroke="var(--ink)" stroke-width="0.8"><circle cx="5" cy="5" r="4.3"/><ellipse cx="5" cy="5" rx="1.9" ry="4.3"/><line x1="0.7" y1="5" x2="9.3" y2="5"/><line x1="1.5" y1="2.7" x2="8.5" y2="2.7"/><line x1="1.5" y1="7.3" x2="8.5" y2="7.3"/></svg>
        varkoworks.com
      </li>
      <li>
        <svg viewBox="0 0 10 10"><rect x="0.3" y="2" width="9.4" height="6.2" fill="var(--ink)"/><polyline points="0.6,2.3 5,5.6 9.4,2.3" fill="none" stroke="var(--white)" stroke-width="0.8"/></svg>
        martin@plumlinegroup.com
      </li>
    </ul>
  </section>

</body>
</html>
```